Business Card Design Project

We are not a new company, but renamed to "Vantorin Kitchens" last year. We specialize in modern high-end cabinetry imports. We would like to communicate a sense of quality and cutting edge technology. Ideally the design would incorporate our logo colors, silver, red and preferably a black, matte background. Though we are open to suggestions.
Logo is attached.
Edit: I have attached rough drafts of the previous cards, this way you will have all necessary content that needs to go on the cards.
Updates
Project Deadline Extended
Reason: We have received a lot of great designs, but due to the sheer number we couldn't respond to all. We will extend the deadline for another 7 days to finalize and provide feedback to designers.
Thank you for your hard work!
Industry/Entity Type
Business
Look and feel
Each slider illustrates characteristics of the customer's brand and the style your logo design should communicate.

```html
<!DOCTYPE html>
<html lang="en">
<head>
<meta charset="utf-8">
<title>Vantorin Kitchens – Business Card</title>
<link href="https://fonts.googleapis.com/css2?family=Arimo:wght@400;700&display=swap" rel="stylesheet">
<style>
  :root {
    --page: #e9e9ee;
    --matte-top: #2a2a2c;
    --matte-bottom: #111112;
    --silver: #c9cacd;
    --silver-light: #e4e5e7;
    --silver-dark: #9c9ea2;
    --red: #e3161d;
    --white: #ffffff;
  }
  * { margin: 0; padding: 0; box-sizing: border-box; }
  html, body { width: 1200px; height: 987px; overflow: hidden; background: var(--page); }
  body { position: relative; font-family: "Arimo", Arial, sans-serif; }

  .card {
    position: absolute;
    width: 700px;
    height: 400px;
    border-radius: 28px;
    overflow: hidden;
    background: linear-gradient(160deg, var(--matte-top), var(--matte-bottom));
    box-shadow: 0 10px 30px rgba(0,0,0,0.18);
  }
  .card-back { left: 440px; top: 50px; }
  .card-front { left: 60px; top: 537px; }

  .card-shape { position: absolute; inset: 0; width: 100%; height: 100%; }

  .brand {
    position: absolute;
    display: flex;
    align-items: center;
    gap: 14px;
    color: var(--silver);
    font-weight: 700;
    font-size: 40px;
    letter-spacing: 3px;
    text-transform: uppercase;
    white-space: nowrap;
  }
  .brand-mark { width: 30px; height: 30px; background: var(--silver); flex: none; }
  .card-back .brand { left: 0; right: 0; top: 172px; justify-content: center; }
  .card-front .brand { left: 0; right: 0; top: 62px; justify-content: center; }

  .holder {
    position: absolute;
    left: 330px;
    top: 168px;
    color: var(--white);
    font-size: 20px;
    letter-spacing: 1px;
    text-transform: uppercase;
  }
  .holder-role { color: var(--red); font-weight: 700; text-transform: none; letter-spacing: 0; }

  .contact {
    position: absolute;
    left: 40px;
    top: 256px;
    list-style: none;
    color: var(--white);
    font-size: 17px;
    line-height: 30px;
  }
  .contact li { display: flex; align-items: center; gap: 20px; }
  .contact-item { display: inline-flex; align-items: center; gap: 7px; }
  .icon { width: 15px; height: 15px; fill: var(--red); flex: none; }
</style>
</head>
<body>

<section class="card card-back" aria-label="Card back">
  <div class="brand"><span class="brand-mark"></span>Vantorin Kitchens</div>
</section>

<section class="card card-front" aria-label="Card front">
  <svg class="card-shape" viewBox="0 0 700 400" preserveAspectRatio="none" aria-hidden="true">
    <defs>
      <linearGradient id="silver-band" x1="0" y1="0" x2="1" y2="1">
        <stop offset="0" stop-color="var(--silver-dark)"/>
        <stop offset="0.55" stop-color="var(--silver)"/>
        <stop offset="1" stop-color="var(--silver-light)"/>
      </linearGradient>
    </defs>
    <path d="M0,138 C240,180 480,262 700,338 L700,400 L0,400 Z" fill="url(#silver-band)"/>
    <path d="M0,128 C240,170 480,252 700,328" fill="none" stroke="var(--red)" stroke-width="7"/>
  </svg>

  <div class="brand"><span class="brand-mark"></span>Vantorin Kitchens</div>

  <p class="holder">Marcus Delane, <span class="holder-role">Director</span></p>

  <ul class="contact">
    <li>
      <span class="contact-item">
        <svg class="icon" viewBox="0 0 16 16" aria-label="Office"><path d="M3.5 1.5l2.5 0 1 3.5-1.8 1.2a8 8 0 0 0 4.6 4.6L11 9l3.5 1v2.5c0 1-1 2-2 2C6.5 14.5 1.5 9.5 1.5 3.5c0-1 1-2 2-2z"/></svg>
        780.555.0142
      </span>
      <span class="contact-item">
        <svg class="icon" viewBox="0 0 16 16" aria-label="Fax"><path d="M4 1h8v4H4zM1 6h14v7h-3v2H4v-2H1zM5 10v4h6v-4z"/></svg>
        780.555.0163
      </span>
    </li>
    <li>
      <span class="contact-item">
        <svg class="icon" viewBox="0 0 16 16" aria-label="Mobile"><path d="M4 0h8a1 1 0 0 1 1 1v14a1 1 0 0 1-1 1H4a1 1 0 0 1-1-1V1a1 1 0 0 1 1-1zm1 2v9h6V2zm3 10.5a1 1 0 1 0 0 2 1 1 0 0 0 0-2z"/></svg>
        780.555.0187
      </span>
      <span class="contact-item">
        <svg class="icon" viewBox="0 0 16 16" aria-label="Email"><path d="M1 3h14v10H1zm1.5 1.5v.3L8 9l5.5-4.2v-.3zM2.5 6.7v4.8h11V6.7L8 11z"/></svg>
        marcus@vantorinkitchens.ca
      </span>
    </li>
    <li>1580 - 42 Ave. Calgary, AB T2G 4K9</li>
  </ul>
</section>

</body>
</html>
```